Fitness Equipment Repair Business Needs a Catchy New Business Card

We have an existing business card, however, it is quite plain and boring. We are expanding primarily in the commercial area (gyms, studios, apartment complexes etc). The business card will serve as eye candy to those managers/owners that can't be met for a face to face.
Originally I was planning for a brochure as well, but all of our information is better summarized on our website. (brightloopservice.ca).
I would like the card to match the colour scheme of the website and utilize the logo. It should have a professional clean feel to it, however, a little colouring outside the lines wouldn't hurt.
The example card is for my service technician (Colin Marsh). If possible I would like to be able to edit the text to use for more than one person.

Industry/Entity Type

Appliance Repair

Contact Information for Business Card

Clean, crisp and professional but needs to be eye catching. Preferably using the black, white and red colour scheme matching the website. Double sided would be nice, but is not necessary.

Colors
ec1f27
ffffff
000000

Requirements
Must have
• Must be able to edit name, phone number and title to use for multiple people. Must show the company website (brightloopservice.ca).

```html
<!DOCTYPE html>
<html lang="en">
<head>
<meta charset="utf-8">
<title>Brightloop Service – Business Card</title>
<link href="https://fonts.googleapis.com/css2?family=Marcellus+SC&family=PT+Sans:wght@400;700&display=swap" rel="stylesheet">
<style>
  :root {
    --red: #ec1f27;
    --white: #ffffff;
    --black: #000000;
    --ink: #1a1a1a;
    --rule: #f2a3a6;
    --bg-top: #2b2b2b;
    --bg-bottom: #000000;
  }
  * { margin: 0; padding: 0; box-sizing: border-box; }
  html, body { width: 1200px; height: 900px; overflow: hidden; }
  body {
    position: relative;
    background: linear-gradient(180deg, var(--bg-top) 0%, #141414 55%, var(--bg-bottom) 100%);
    font-family: "PT Sans", Arial, sans-serif;
    color: var(--ink);
  }
  .card {
    position: absolute;
    top: 306px;
    height: 271px;
    background: var(--white);
    border-radius: 10px;
    overflow: hidden;
  }
  .card-front { left: 149px; width: 439px; }
  .card-back { left: 608px; width: 441px; }

  .brand { position: absolute; display: flex; align-items: center; }
  .brand-mark { background: var(--black); flex: none; }
  .brand-name {
    font-family: "Marcellus SC", Georgia, serif;
    color: var(--black);
    font-weight: 400;
    line-height: 1.25;
  }
  .card-front .brand { left: 30px; top: 40px; gap: 28px; }
  .card-front .brand-mark { width: 52px; height: 52px; }
  .card-front .brand-name { font-size: 28px; }
  .card-back .brand { left: 95px; top: 62px; gap: 40px; }
  .card-back .brand-mark { width: 66px; height: 66px; }
  .card-back .brand-name { font-size: 36px; }

  .person { position: absolute; right: 22px; top: 143px; text-align: right; }
  .person-name { color: var(--red); font-weight: 700; font-size: 15px; line-height: 18px; }
  .person-title { font-size: 12px; line-height: 15px; }

  .divider { position: absolute; left: 29px; right: 22px; top: 182px; height: 1px; background: var(--rule); }

  .contacts { position: absolute; left: 27px; top: 187px; list-style: none; font-size: 12px; line-height: 16px; }
  .contacts li { display: flex; align-items: center; gap: 6px; }
  .contacts svg { width: 9px; height: 9px; fill: var(--red); flex: none; }

  .address { position: absolute; right: 22px; top: 191px; text-align: right; font-size: 12px; line-height: 20px; font-style: normal; }

  .tagline { position: absolute; left: 0; right: 0; top: 213px; text-align: center; color: var(--red); font-size: 12.5px; }
</style>
</head>
<body>
  <section class="card card-front">
    <div class="brand">
      <span class="brand-mark"></span>
      <div class="brand-name">Brightloop<br>Service</div>
    </div>
    <div class="person">
      <div class="person-name">Colin Marsh</div>
      <div class="person-title">Managing Director</div>
    </div>
    <div class="divider"></div>
    <ul class="contacts">
      <li><svg viewBox="0 0 10 10"><rect x="2.5" y="0" width="5" height="10" rx="1"/><rect x="3.5" y="1.2" width="3" height="6" fill="#fff"/></svg>044-555 010 234</li>
      <li><svg viewBox="0 0 10 10"><path d="M2 0.5l2 2-1 1.2c.6 1.3 1.6 2.3 2.9 2.9l1.2-1 2 2-1.3 1.9C4 9 1 6 .5 1.8z"/></svg>044-555 010 234</li>
      <li><svg viewBox="0 0 10 10"><rect x="0" y="2" width="10" height="6"/><path d="M0 2l5 3.5L10 2" stroke="#fff" stroke-width="0.8" fill="none"/></svg>info@brightloopservice.ca</li>
      <li><svg viewBox="0 0 10 10"><circle cx="5" cy="5" r="5"/><path d="M0 5h10M5 0c-2 2.5-2 7.5 0 10M5 0c2 2.5 2 7.5 0 10" stroke="#fff" stroke-width="0.7" fill="none"/></svg>www.brightloopservice.ca</li>
    </ul>
    <address class="address">12345, Address<br>Goes Here Country<br>Name, 123456.</address>
  </section>

  <section class="card card-back">
    <div class="brand">
      <span class="brand-mark"></span>
      <div class="brand-name">Brightloop<br>Service</div>
    </div>
    <p class="tagline">When your equipment can't finish ther workout, give us a call!</p>
  </section>
</body>
</html>
```